New Business Card Design Project

Use the flyer uploaded and website www.brightoakbuilders.com for inspiration.
List Our Services on Backside of business cards
Marcus Delling
Harborline Builders Inc.
Licensed General Contractors
858-471-6093

Contact Information for Business Card

Use the flyer uploaded and website www.brightoakbuilders.com for inspiration. List Our Services on Backside of business cards Marcus Delling Harborline Builders Inc. Licensed General Contractors 858-471-6093

```html
<!DOCTYPE html>
<html lang="en">
<head>
<meta charset="UTF-8">
<title>Harborline Builders — Business Card</title>
<link href="https://fonts.googleapis.com/css2?family=Cinzel:wght@400;500&family=Roboto:wght@400;500&display=swap" rel="stylesheet">
<style>
  :root {
    --bg: #2b2b2b;
    --card: #121212;
    --card-edge: #1c1c1c;
    --white: #f4f4f4;
    --blue: #2f80d4;
    --red: #e3161f;
    --rule: #5a5a5a;
    --pattern-hi: #262626;
    --pattern-lo: #151515;
  }
  * { box-sizing: border-box; margin: 0; padding: 0; }
  html, body { width: 1200px; height: 1108px; overflow: hidden; background: var(--bg); }
  .canvas {
    width: 1200px; height: 1108px;
    display: flex; align-items: center; justify-content: center; gap: 60px;
  }
  .card {
    width: 420px; height: 660px;
    background: var(--card);
    border-radius: 26px;
    box-shadow: 0 18px 40px rgba(0,0,0,.45);
    position: relative; overflow: hidden;
    color: var(--white);
    font-family: "Roboto", Arial, sans-serif;
  }
  /* Front */
  .card-front { display: flex; flex-direction: column; align-items: center; }
  .brand {
    margin-top: 190px;
    display: flex; align-items: center; gap: 14px;
    font-family: "Cinzel", Georgia, serif;
    font-size: 27px; font-weight: 400; letter-spacing: 1px;
    color: var(--white);
  }
  .brand-mark { width: 12px; height: 12px; background: var(--white); }
  .holder-name {
    margin-top: 170px;
    font-family: "Cinzel", Georgia, serif;
    font-size: 32px; font-weight: 500; color: var(--blue); letter-spacing: .5px;
  }
  .icon-rule {
    margin-top: 14px; width: 300px;
    display: flex; align-items: center; gap: 8px;
  }
  .icon-rule .line { flex: 1; height: 1px; background: var(--rule); }
  .icon-box {
    width: 30px; height: 30px; border-radius: 5px; background: var(--blue);
    display: flex; align-items: center; justify-content: center;
  }
  .icon-box svg { width: 18px; height: 18px; }
  .contacts {
    margin-top: 14px; text-align: center;
    font-size: 19px; line-height: 1.4; color: var(--white);
  }
  .divider { margin-top: 18px; width: 300px; height: 1px; background: var(--rule); }
  .legal {
    margin-top: 14px; text-align: center; color: var(--red);
    font-size: 19px; line-height: 1.4;
  }
  /* Back */
  .pattern {
    position: absolute; inset: 0;
    background: linear-gradient(160deg, var(--pattern-hi) 0%, var(--pattern-lo) 70%);
  }
  .services {
    position: absolute; left: 0; right: 0; top: 300px;
    list-style: none; text-align: center;
    font-size: 22px; line-height: 1.48; color: var(--white);
  }
</style>
</head>
<body>
<main class="canvas">
  <section class="card card-front">
    <div class="brand"><span class="brand-mark"></span>Harborline Builders</div>

    <h1 class="holder-name">Marcus Delling</h1>

    <div class="icon-rule">
      <span class="line"></span>
      <span class="icon-box" aria-label="Phone">
        <svg viewBox="0 0 24 24" fill="#121212"><path d="M6.6 10.8a15 15 0 0 0 6.6 6.6l2.2-2.2c.3-.3.7-.4 1-.2 1.1.4 2.3.6 3.6.6.6 0 1 .4 1 1V20c0 .6-.4 1-1 1A17 17 0 0 1 3 4c0-.6.4-1 1-1h3.5c.6 0 1 .4 1 1 0 1.3.2 2.5.6 3.6.1.3 0 .7-.2 1z"/></svg>
      </span>
      <span class="icon-box" aria-label="Email">
        <svg viewBox="0 0 24 24" fill="none" stroke="#121212" stroke-width="2"><rect x="3" y="6" width="18" height="12" rx="1"/><path d="M3 6l9 7 9-7"/></svg>
      </span>
      <span class="icon-box" aria-label="Website">
        <svg viewBox="0 0 24 24" fill="none" stroke="#121212" stroke-width="2"><circle cx="12" cy="12" r="9"/><path d="M3 12h18M12 3c3 3 3 15 0 18M12 3c-3 3-3 15 0 18"/></svg>
      </span>
      <span class="line"></span>
    </div>

    <div class="contacts">
      <p>858-471-6093</p>
      <p>info@brightoakbuilders.com</p>
      <p>www.brightoakbuilders.com</p>
    </div>

    <div class="divider"></div>

    <div class="legal">
      <p>Harborline Builders Inc.</p>
      <p>Licensed General Contractors</p>
    </div>
  </section>

  <section class="card card-back">
    <div class="pattern" role="img" aria-label="Faint repeating house and palm tree pattern"></div>
    <ul class="services">
      <li>Remodel: Kitchen &amp; Bath</li>
      <li>Painting: Interior &amp; Exterior</li>
      <li>Flooring: Carpet, Vinyl, Wood</li>
      <li>Window &amp; Door Replacement</li>
      <li>Plumbing: Repairs &amp; Upgrades</li>
      <li>Energy-Efficient Upgrades</li>
      <li>Deck &amp; Patio Construction</li>
      <li>Water &amp; Mold Damage</li>
      <li>Garage Renovation</li>
    </ul>
  </section>
</main>
</body>
</html>
```